Landing Page / Waitlist

I would like a landing page for people to sign up for a waiting list. The text on the page should include (but is not limited to):
1) Main point: The accounting system you'll love
2) Secondary points:
a. Ruthlessly efficient
b. Quietly intelligent
c. Driven by AI
I've attached a file of our logo

The design should be simple, clean, and innovative - this is an ai company

```html
<!DOCTYPE html>
<html lang="en">
<head>
<meta charset="UTF-8">
<title>TallyGlow – Join the Waitlist</title>
<link href="https://fonts.googleapis.com/css2?family=Inter:wght@400;500;600;700;800&display=swap" rel="stylesheet">
<style>
  :root {
    --sky-top: #00b4f7;
    --sky-mid: #0aa2f5;
    --sky-deep: #0a8ef2;
    --pill: #0794fb;
    --white: #ffffff;
    --accent-dot: #ffd60a;
    --ink: #1d1d1f;
    --footer-ink: #333333;
    --icon-blue: #0b97f3;
  }
  * { margin: 0; padding: 0; box-sizing: border-box; }
  html, body { width: 1200px; height: 722px; overflow: hidden; background: var(--white); font-family: "Inter", sans-serif; }
  .page { position: relative; width: 1200px; height: 722px; }
  .hero {
    position: absolute; left: 0; top: 0; width: 1200px; height: 640px; overflow: hidden;
    background: linear-gradient(170deg, var(--sky-top) 0%, var(--sky-mid) 55%, var(--sky-deep) 100%);
    color: var(--white);
  }
  .hero-decor { position: absolute; inset: 0; }
  .brand { position: absolute; left: 0; width: 1200px; top: 52px; display: flex; justify-content: center; align-items: center; gap: 10px; }
  .brand-mark { width: 14px; height: 14px; border-radius: 50%; background: var(--white); }
  .brand-name { font-size: 27px; font-weight: 700; letter-spacing: -0.3px; }
  .headline { position: absolute; left: 0; width: 1200px; top: 176px; text-align: center; font-size: 47px; font-weight: 800; line-height: 53px; letter-spacing: -0.3px; }
  .intro { position: absolute; left: 250px; width: 700px; top: 296px; text-align: center; font-size: 12.6px; line-height: 20px; }
  .signup { position: absolute; left: 250px; top: 377px; width: 700px; height: 97px; border-radius: 49px;
    background: linear-gradient(180deg, #0a8efc 0%, #05b0fb 100%); }
  .email-field { position: absolute; left: 46px; top: 29px; width: 394px; height: 39px; border: 2px solid var(--white); border-radius: 20px;
    background: transparent; color: var(--white); font: 400 14px "Inter", sans-serif; padding-left: 21px; display: flex; align-items: center; }
  .join-button { position: absolute; left: 446px; top: 29px; width: 210px; height: 39px; border-radius: 20px; background: var(--white);
    color: var(--ink); font: 600 16px "Inter", sans-serif; display: flex; align-items: center; justify-content: center; }
  .note { position: absolute; left: 0; width: 1200px; top: 488px; text-align: center; font-size: 13.5px; }
  .feature { position: absolute; width: 65px; height: 65px; border-radius: 50%; background: var(--white);
    box-shadow: 0 6px 18px rgba(0, 60, 140, 0.25); display: flex; align-items: center; justify-content: center; }
  .feature svg { width: 34px; height: 34px; }
  .feature-label { position: absolute; font-size: 11.5px; font-weight: 600; line-height: 18px; }
  .footer { position: absolute; left: 0; top: 640px; width: 1200px; height: 82px; display: flex; align-items: center; justify-content: center;
    font-size: 15px; color: var(--footer-ink); gap: 6px; }
</style>
</head>
<body>
<div class="page">
  <section class="hero">
    <svg class="hero-decor" width="1200" height="640" viewBox="0 0 1200 640" aria-hidden="true">
      <path d="M0 40 C 250 80, 500 0, 800 40 S 1100 60, 1200 20 L1200 0 L0 0 Z" fill="#ffffff" opacity="0.05"/>
      <path d="M0 420 C 300 520, 700 460, 1200 560 L1200 640 L0 640 Z" fill="#0a7fe6" opacity="0.25"/>
      <g fill="none" stroke="#ffffff" stroke-opacity="0.3" stroke-width="1">
        <circle cx="600" cy="320" r="325"/>
        <circle cx="600" cy="320" r="402"/>
        <circle cx="600" cy="320" r="476"/>
      </g>
      <g fill="var(--accent-dot)">
        <circle cx="386" cy="74" r="5"/>
        <circle cx="138" cy="202" r="5"/>
        <circle cx="1052" cy="174" r="5"/>
        <circle cx="270" cy="551" r="5"/>
      </g>
      <g fill="none" stroke="#8ccfff" stroke-width="4" stroke-linejoin="round" opacity="0.8">
        <path d="M222 465 L250 478 L222 492 Z"/>
        <path d="M812 545 L840 558 L812 572 Z"/>
      </g>
    </svg>

    <div class="brand">
      <span class="brand-mark"></span>
      <span class="brand-name">TallyGlow</span>
    </div>

    <h1 class="headline">The Accounting<br>System You'll Love</h1>

    <p class="intro">Lorem ipsum dolor sit amet, consectetur adipiscing elit, sed do eiusmod tempor incididunt ut labore et dolore magna aliqua. Ut enim ad minim veniam, quis nostrud exercitation ullamco laboris nisi ut aliquip ex ea commodo consequat. reprehenderit in voluptate velit esse cillum dolore eu fugiat nulla pariatur.</p>

    <form class="signup">
      <div class="email-field">Enter your email</div>
      <div class="join-button">Join the Waitlist</div>
    </form>

    <p class="note">Be among the first to experience TallyGlow.</p>

    <div class="feature" style="left:849px; top:127px;">
      <svg viewBox="0 0 34 34" aria-hidden="true">
        <path d="M15 6 C9 6 7 10 8 13 C5 15 6 20 8 21 C7 25 11 28 15 27 Z" fill="var(--icon-blue)"/>
        <path d="M18 6 C22 6 25 8 25 11 C28 13 28 19 25 21 C25 25 22 28 18 27 Z" fill="var(--icon-blue)"/>
        <g fill="none" stroke="#fff" stroke-width="1.4">
          <path d="M18 12 H22"/><circle cx="23.5" cy="12" r="1.4"/>
          <path d="M18 17 H24"/><circle cx="25.5" cy="17" r="1.4"/>
          <path d="M18 22 H22"/><circle cx="23.5" cy="22" r="1.4"/>
        </g>
      </svg>
    </div>
    <div class="feature-label" style="left:915px; top:173px;">Quietly<br>Intelligent</div>

    <div class="feature" style="left:155px; top:304px;">
      <svg viewBox="0 0 34 34" aria-hidden="true">
        <path d="M17 8 C12 8 9 11 9 15 C9 18 11 20 12.5 21.5 V24 H21.5 V21.5 C23 20 25 18 25 15 C25 11 22 8 17 8 Z" fill="var(--icon-blue)"/>
        <path d="M18 11 L14 17 H17 L16 21 L20 15 H17 Z" fill="#fff"/>
        <rect x="13" y="25.5" width="8" height="1.6" rx="0.8" fill="var(--icon-blue)"/>
        <rect x="14" y="28" width="6" height="1.6" rx="0.8" fill="var(--icon-blue)"/>
        <g stroke="var(--icon-blue)" stroke-width="1.4" stroke-linecap="round">
          <path d="M17 3 V5"/><path d="M7 7 L8.5 8.5"/><path d="M27 7 L25.5 8.5"/><path d="M3.5 15 H5.5"/><path d="M28.5 15 H30.5"/>
        </g>
      </svg>
    </div>
    <div class="feature-label" style="left:95px; top:366px; text-align:right; width:70px;">Ruthlessly<br>Efficient</div>

    <div class="feature" style="left:992px; top:491px;">
      <svg viewBox="0 0 34 34" aria-hidden="true">
        <rect x="8" y="8" width="18" height="18" rx="3" fill="var(--icon-blue)"/>
        <g stroke="var(--icon-blue)" stroke-width="1.4">
          <path d="M12 4 V8 M17 4 V8 M22 4 V8 M12 26 V30 M17 26 V30 M22 26 V30 M4 12 H8 M4 17 H8 M4 22 H8 M26 12 H30 M26 17 H30 M26 22 H30"/>
        </g>
        <text x="17" y="21" text-anchor="middle" font-family="Inter, sans-serif" font-weight="700" font-size="10" fill="#fff">AI</text>
      </svg>
    </div>
    <div class="feature-label" style="left:1058px; top:537px;">Driven<br>by AI</div>
  </section>

  <footer class="footer">
    <span>©</span><span>Copyrights 2025 | All Rights Reserved</span>
  </footer>
</div>
</body>
</html>
```